"Word Cloud" lists of countries, by decade, who have adopted women's suffrage

The winning designer will (eventually, but not necessarily within this project--see "Nice to Haves", below) design a total of eight images, based on the eight lists of countries (see attached files) in order, by decade, that they adopted women's suffrage.

One of the the attached images is a screen shot of five pages of the book RISE: The Argument for The Realm of Stars, showing how these lists are presently arranged on 6"x9" pages.

We essentially want to spice up these 8 lists and make them more fun to look at, for the reader.

Target Market(s)

General audience. People who want to make a difference. People who want to do something to change the world, and want to read a book about how we can actually do it.

Industry/Entity Type

Political

Font styles to use
Serif
Sans Serif
Decorative
Script

Requirements
Must have
• At least two initial designs, one for each of the two largest lists (lists 5 and 6). All country names must be spelled correctly. A WORD doc has been provided with all the text you need to work with. An EXAMPLE word cloud has been provided for inspiration. The look and feel of these "Country Clouds" wants to go all over the place, but all names should be (at least somewhat) readable.
• IMPORTANT ELEMENTS: (1) There are a few places where current countries were just one, when they got women's suffrage. Keep this info intact, together, in the cloud. EXAMPLE (from list 6):
•  British Leeward Islands (remove ", including today’s:", but keep together with)
•  Antigua and Barbuda
•  British Virgin Islands
•  Montserrat
•  Saint Kitts and Nevis
•  Anguilla
• (2) The names of the countries should stay in roughly the same order as found in the lists, but laid out (very) roughly right to left and then top to bottom, loosely akin to the standard flow of text written in the latin alphabet. It is fine to alter this standard in minor ways to achieve a better look to the design. Just don't move a country found at the top of one list into the middle of that list or down to the bottom, etc.
• These country clouds will be printed in black and white, so keep the designs greyscale.
• These "country clouds" should be 4.5" in width.The largest country clouds, with the most countries found in them, should not exceed 6" in length.
Nice to have
• (Eventually) all 8 lists in the form of "Country Clouds"---that are playful, but with serious elements. Pull up a list of countries by population, have the 20 biggest use the biggest font sizes. Use many different fonts, mix it up! Essentially, these 8 lists all want to become word clouds, with each nation's full name as its own "word." See example cloud.
• Though having all 8 lists in clouds at the end of this project is "nice to have," the winner for this design might simply produce 2 such clouds, along with a cost estimate attached to the submitted design for what they would charge to complete the other 6 clouds.
Should not have
• Do NOT include the textual transitions found between the lists, in the screen shot or word doc. They are there just to help you see how the different graphics will be used and what will go either before or after them.
• No need to use bullet points.

```html
<!DOCTYPE html>
<html lang="en">
<head>
<meta charset="utf-8">
<title>Country Cloud</title>
<link rel="stylesheet" href="https://fonts.googleapis.com/css2?family=Alfa+Slab+One&family=Arvo:wght@700&family=Audiowide&family=Cormorant+Garamond:wght@300&family=Federo&family=Great+Vibes&family=Kaushan+Script&family=Montserrat:wght@700&family=Oswald:wght@600&family=Playfair+Display:wght@400;900&family=Raleway:wght@200&family=Rye&family=Stardos+Stencil:wght@700&display=swap">
<style>
  :root {
    --paper-center: #ffffff;
    --paper-edge: #e0e0e0;
    --ink-dark: #3d3d3d;
    --ink-deep: #474747;
    --ink-mid: #5a5a5a;
    --ink-soft: #6e6e6e;
    --ink-light: #8c8c8c;
    --ink-pale: #9e9e9e;
  }
  html, body {
    margin: 0;
    padding: 0;
    width: 985px;
    height: 1200px;
    overflow: hidden;
  }
  .country-cloud {
    display: block;
    width: 985px;
    height: 1200px;
    background: radial-gradient(ellipse at 50% 55%, var(--paper-center) 0%, #f4f4f4 40%, var(--paper-edge) 100%);
  }
  .name { text-rendering: geometricPrecision; }
  .albania      { font-family: "Alfa Slab One", serif; font-size: 42px; fill: var(--ink-deep); }
  .czechoslovakia { font-family: "Playfair Display", serif; font-weight: 400; font-size: 56px; fill: var(--ink-light); }
  .czech-republic { font-family: "Kaushan Script", cursive; font-size: 50px; fill: var(--ink-soft); }
  .slovakia     { font-family: "Arvo", serif; font-weight: 700; font-size: 96px; fill: var(--ink-deep); }
  .united-states { font-family: "Stardos Stencil", serif; font-weight: 700; font-size: 86px; fill: var(--ink-mid); }
  .sweden       { font-family: "Playfair Display", serif; font-weight: 900; font-size: 80px; fill: var(--ink-light); }
  .burma        { font-family: "Great Vibes", cursive; font-size: 90px; fill: var(--ink-soft); }
  .kazakhstan   { font-family: "Audiowide", sans-serif; font-size: 66px; fill: var(--ink-deep); }
  .mongolia     { font-family: "Raleway", sans-serif; font-weight: 200; font-size: 62px; fill: var(--ink-light); }
  .tajikistan   { font-family: "Rye", serif; font-size: 84px; fill: var(--ink-light); }
  .turkmenistan { font-family: "Cormorant Garamond", serif; font-weight: 300; font-size: 96px; fill: var(--ink-mid); }
  .italy        { font-family: "Playfair Display", serif; font-weight: 400; font-size: 212px; fill: var(--ink-dark); }
  .trinidad     { font-family: "Raleway", sans-serif; font-weight: 200; font-size: 78px; fill: var(--ink-pale); }
  .equador      { font-family: "Rye", serif; font-size: 76px; fill: var(--ink-soft); }
  .moldova      { font-family: "Oswald", sans-serif; font-weight: 600; font-size: 56px; fill: var(--ink-mid); }
  .puerto-rico  { font-family: "Federo", sans-serif; font-size: 88px; fill: var(--ink-soft); }
  .romania      { font-family: "Montserrat", sans-serif; font-weight: 700; font-size: 46px; fill: var(--ink-soft); }
</style>
</head>
<body>
<svg class="country-cloud" width="985" height="1200" viewBox="0 0 985 1200" xmlns="http://www.w3.org/2000/svg" aria-label="Countries adopting women's suffrage">
  <text class="name albania" x="132" y="142" textLength="746" lengthAdjust="spacingAndGlyphs">THE PRINCIPALITY OF ALBANIA</text>
  <text class="name czechoslovakia" x="118" y="200" textLength="446" lengthAdjust="spacingAndGlyphs">CZECHOSLOVAKIA</text>
  <text class="name czech-republic" x="570" y="196" textLength="326" lengthAdjust="spacingAndGlyphs">Czech Republic</text>

  <text class="name slovakia" transform="translate(104,220) rotate(90)" x="0" y="0" textLength="560" lengthAdjust="spacingAndGlyphs">SLOVAKIA</text>

  <text class="name united-states" x="188" y="288" textLength="704" lengthAdjust="spacingAndGlyphs">UNITED STATES</text>
  <text class="name sweden" x="190" y="364" textLength="462" lengthAdjust="spacingAndGlyphs">SWEDEN</text>
  <text class="name burma" x="660" y="376" textLength="228" lengthAdjust="spacingAndGlyphs">Burma</text>
  <text class="name kazakhstan" x="190" y="452" textLength="644" lengthAdjust="spacingAndGlyphs">KAZAKHSTAN</text>

  <text class="name mongolia" transform="translate(856,404) rotate(90)" x="0" y="0" textLength="372" lengthAdjust="spacingAndGlyphs">MONGOLIA</text>

  <text class="name tajikistan" x="180" y="532" textLength="664" lengthAdjust="spacingAndGlyphs">TAJIKISTAN</text>
  <text class="name turkmenistan" x="200" y="608" textLength="644" lengthAdjust="spacingAndGlyphs">TURKMENISTAN</text>
  <text class="name italy" x="200" y="776" textLength="608" lengthAdjust="spacingAndGlyphs">ITALY</text>
  <text class="name trinidad" x="118" y="848" textLength="778" lengthAdjust="spacingAndGlyphs">TRINIDAD AND TOBAGO</text>
  <text class="name equador" x="104" y="920" textLength="536" lengthAdjust="spacingAndGlyphs">EQUADOR</text>
  <text class="name moldova" x="662" y="924" textLength="226" lengthAdjust="spacingAndGlyphs">MOLDOVA</text>
  <text class="name puerto-rico" x="118" y="1012" textLength="770" lengthAdjust="spacingAndGlyphs">PUERTO RICO</text>
  <text class="name romania" x="116" y="1088" textLength="276" lengthAdjust="spacingAndGlyphs">ROMANIA</text>
</svg>
</body>
</html>
```